Contact card for an aggressive entrepreneur

I am looking for a business/contact card as an individual. I operate under the company name The Varsk Holdings, LLC (but don't generally use that other than for billing). I have explored a few ideas and am now turning to artmarketly to connect with people more creative than me. I am trying to capture a diverse set of passions, which I will summarize with the following keywords (which may or may not be ON the card and are in no particular order):

entrepreneur
shark diver
MBA
visionary
defenseman
marketing guru
hockey coach
teacher
reader
writer
cook
captain
scuba diver
beach bum
Type A
Columbia
Vermont
New York
Montauk
founder
leader
focused
driven
teammate father

hope that makes some sense!
Updates

Please note the photo is for reference - unless there is a really creative way to use it I do not need a card with a head shot (I am not a model or an actor!)

Project Deadline Extended
Reason: There have been several requests to submit designs so we will close this project this Wednesday and select a design by this Friday. Thank you to all for your great ideas and submissions!

I am reviewing the designs and will select one by end of day tomorrow, Tuesday, EST
Thank you to all who participated!

Target Market(s)

everyone from business contacts to personal acquaintances

Industry/Entity Type

Business

Requirements
Must have
• Must be utterly original, extraordinary and memorable.
How it achieves that is up to you!
Essential contact information that needs to be included:

phone: (555) 014-3927
email: tomas@varskholdings.example
skype: tomas.varsk
Nice to have
• A striking visual whether that is a photo or illustration
Some way of conveying the diversity of what I am and what I do
Feel free to use the printing or physical material of the card to make it stand out.
Should not have
• I am not into "logos" but that being said I do not want to limit creativity in any way so feel free to ignore any part of this brief if you disagree with me. No need to use the attached photo of me, but that's what I look like.

```html
<!DOCTYPE html>
<html lang="en">
<head>
<meta charset="utf-8">
<title>Tomas Varsk – Contact Card</title>
<link rel="stylesheet" href="https://fonts.googleapis.com/css2?family=Poiret+One&family=Questrial&display=swap">
<style>
  :root {
    --board-light: #e4e1df;
    --board-mid: #d3cdcc;
    --board-edge: #c4bebd;
    --footer-bar: #1a1810;
    --card-dark: #1b1b1b;
    --photo-deep: #141414;
    --photo-mid: #2e2e2e;
    --photo-light: #555555;
    --umbrella-yellow: #e3cc2c;
    --umbrella-shade: #b59d1e;
    --accent-yellow: #fde442;
    --back-yellow: #f5eb6e;
    --label-yellow: #e8cf3a;
    --label-blue: #8fb8d6;
    --text-light: #f2f2f2;
  }
  * { margin: 0; padding: 0; box-sizing: border-box; }
  html, body { width: 921px; height: 1200px; overflow: hidden; }
  body {
    position: relative;
    background: radial-gradient(ellipse at 50% 40%, var(--board-light) 0%, var(--board-mid) 60%, var(--board-edge) 100%);
    font-family: "Questrial", sans-serif;
  }
  .card {
    position: absolute;
    left: 99px;
    width: 724px;
    height: 418px;
    box-shadow: 0 6px 14px rgba(0, 0, 0, 0.28);
  }
  .card--front { top: 123px; background: var(--card-dark); overflow: hidden; }
  .card--back { top: 636px; height: 421px; background: var(--back-yellow); }
  .card__photo {
    position: absolute;
    inset: 0 0 37px 0;
    background:
      radial-gradient(ellipse 200px 90px at 487px 245px, var(--umbrella-yellow) 0%, var(--umbrella-yellow) 55%, var(--umbrella-shade) 80%, rgba(181, 157, 30, 0) 100%),
      radial-gradient(ellipse 60% 50% at 25% 60%, rgba(110, 110, 110, 0.55), rgba(110, 110, 110, 0) 100%),
      linear-gradient(180deg, var(--photo-deep) 0%, var(--photo-mid) 35%, var(--photo-light) 60%, var(--photo-mid) 85%, var(--photo-deep) 100%);
  }
  .card__band {
    position: absolute;
    left: 0; right: 0; bottom: 0;
    height: 37px;
    background: var(--accent-yellow);
  }
  .card__name {
    position: absolute;
    right: 52px;
    top: 86px;
    font-family: "Poiret One", sans-serif;
    font-weight: 400;
    font-size: 36px;
    letter-spacing: 0.5px;
    color: var(--text-light);
    line-height: 1;
  }
  .card__rule {
    position: absolute;
    left: 37px;
    right: 52px;
    top: 130px;
    height: 2px;
    background: var(--accent-yellow);
  }
  .contact {
    position: absolute;
    left: 37px;
    top: 266px;
    list-style: none;
    font-size: 17px;
    line-height: 28.5px;
    color: var(--text-light);
    letter-spacing: 0.4px;
  }
  .contact__label--yellow { color: var(--label-yellow); }
  .contact__label--blue { color: var(--label-blue); }
  .footer-bar {
    position: absolute;
    left: 0; right: 0; bottom: 0;
    height: 47px;
    background: var(--footer-bar);
  }
</style>
</head>
<body>
  <section class="card card--front" aria-label="Card front">
    <div class="card__photo" role="img" aria-label="Photo of a crowd of black umbrellas with a single yellow umbrella standing out on the right"></div>
    <h1 class="card__name">TOMAS VARSK</h1>
    <div class="card__rule"></div>
    <ul class="contact">
      <li><span class="contact__label--yellow">Ph:</span> (555) 014-3927</li>
      <li><span class="contact__label--yellow">Email:</span> tomas@varskholdings.example</li>
      <li><span class="contact__label--blue">skype:</span> tomas.varsk</li>
    </ul>
    <div class="card__band"></div>
  </section>

  <section class="card card--back" aria-label="Card back"></section>

  <div class="footer-bar"></div>
</body>
</html>
```